DELCOURT ROOFING YARD SIGN

We need a yard sign to put in our customers' yards when we are roofing their home.
Delcourt Roofing
417 Tobin Rd
Lake Charles LA 70615
phone: 337-555-0182

Maybe some verbiage like "Your Hometown Roofing Experts"
or
"Family Owned Since 1956"

```html
<!DOCTYPE html>
<html lang="en">
<head>
<meta charset="UTF-8">
<title>Delcourt Roofing Yard Sign</title>
<link href="https://fonts.googleapis.com/css2?family=Montserrat:wght@500;600;700;800&display=swap" rel="stylesheet">
<style>
  :root {
    --navy: #14123d;
    --black: #000000;
    --charcoal: #2c2c2c;
    --white: #ffffff;
    --ink: #111111;
    --backdrop: #7a7a7a;
  }
  * { margin: 0; padding: 0; box-sizing: border-box; }
  html, body {
    width: 1200px; height: 1200px; overflow: hidden;
    background: var(--backdrop);
    font-family: 'Montserrat', sans-serif;
  }
  .sign {
    position: absolute; left: 30px; top: 173px;
    width: 1140px; height: 854px;
    background: var(--white);
    overflow: hidden;
  }
  .sign-header {
    position: absolute; left: 0; top: 0; width: 100%; height: 327px;
    background: radial-gradient(ellipse at 50% 40%, var(--charcoal) 0%, var(--black) 70%);
  }
  .headline {
    position: absolute; left: 0; top: 30px; width: 100%;
    text-align: center; color: var(--white);
    font-weight: 700; font-size: 88px; line-height: 84px;
    letter-spacing: 1px; word-spacing: 14px;
  }
  .services-band {
    position: absolute; left: 32px; top: 223px; width: 1071px; height: 104px;
    background: var(--navy);
    border-radius: 22px 22px 0 0;
    display: flex; align-items: center; justify-content: center;
    color: var(--white); font-weight: 700; font-size: 56px; letter-spacing: 0.5px;
    word-spacing: 6px;
  }
  .brand-seal {
    position: absolute; left: 34px; top: 356px; width: 400px; height: 400px;
    border-radius: 50%;
    border: 5px solid #cfcfcf;
    box-shadow: inset 0 0 0 3px var(--white), inset 0 0 0 5px #9a9a9a;
    display: flex; align-items: center; justify-content: center;
  }
  .brand-name {
    color: var(--navy); font-weight: 700; font-size: 34px; line-height: 44px;
    text-align: center;
  }
  .phone-icon {
    position: absolute; left: 729px; top: 391px; width: 104px; height: 104px;
  }
  .phone-number {
    position: absolute; left: 450px; top: 495px; width: 670px;
    text-align: center; color: var(--navy);
    font-weight: 800; font-size: 96px; letter-spacing: -2px; line-height: 100px;
  }
  .address {
    position: absolute; left: 470px; top: 595px; width: 630px;
    text-align: center; color: var(--ink);
    font-weight: 500; font-size: 43px; line-height: 46px;
  }
  .tagline-row {
    position: absolute; left: 44px; top: 790px; width: 1057px; height: 50px;
    display: flex; align-items: center; gap: 18px;
  }
  .tagline-rule { flex: 1; height: 5px; background: var(--black); }
  .tagline {
    color: var(--navy); font-weight: 700; font-size: 38px; letter-spacing: 0.5px;
    white-space: nowrap;
  }
</style>
</head>
<body>
  <div class="sign">
    <header class="sign-header">
      <h1 class="headline">YOUR HOMETOWN<br>ROOFING EXPERTS</h1>
      <div class="services-band">ROOFING &bull; SLIDING &bull; CHIMNEYS</div>
    </header>

    <div class="brand-seal">
      <span class="brand-name">DELCOURT<br>ROOFING</span>
    </div>

    <svg class="phone-icon" viewBox="0 0 104 104" aria-hidden="true">
      <circle cx="52" cy="52" r="52" fill="var(--navy)"/>
      <path d="M34 28c3-2 6-2 8 1l5 8c1 2 1 4-1 6l-3 3c2 6 7 11 13 14l3-3c2-2 4-2 6-1l8 5c3 2 3 5 1 8l-3 4c-3 3-8 4-13 2-13-6-23-16-29-29-2-5-1-10 2-13z" fill="var(--white)"/>
      <path d="M56 30a18 18 0 0 1 18 18" stroke="var(--white)" stroke-width="4" fill="none" stroke-linecap="round"/>
      <path d="M57 20a28 28 0 0 1 27 27" stroke="var(--white)" stroke-width="4" fill="none" stroke-linecap="round"/>
      <path d="M55 40a8 8 0 0 1 9 9" stroke="var(--white)" stroke-width="4" fill="none" stroke-linecap="round"/>
    </svg>

    <div class="phone-number">337-555-0182</div>
    <div class="address">417 TOBIN RD<br>LAKE CHARLES LA 70615</div>

    <div class="tagline-row">
      <span class="tagline-rule"></span>
      <span class="tagline">FAMILY OWNED SINCE 1956</span>
      <span class="tagline-rule"></span>
    </div>
  </div>
</body>
</html>
```